Harborlane Products Flyer

Harborlane Lending Group, Inc.
Licensed Mortgage Company
Serving the DMV since 1997
"You open the Harborlane, we'll carry the load"
We specialize in...
FHA Loans
* Credit Scores as low as 500
* 203K Renovation Loans
Conventional Loans
* As little as 1% Down
* Bank Statement for Self-Employed
Investor Loans
* DSCR, & Fix & Flip
* Commercial & New Construction
Other Programs
* HELOCS & Reverse Mortgages
Call today for a free consultation
(800) 914-6027
www.harborlanehomeloans.com
NMLS #731860

```html
<!DOCTYPE html>
<html lang="en">
<head>
<meta charset="utf-8">
<title>Harborlane Products Flyer</title>
<link href="https://fonts.googleapis.com/css2?family=Cinzel:wght@400;600;700&family=Varela+Round&display=swap" rel="stylesheet">
<style>
  :root {
    --navy: #04141e;
    --gold: #d9a53a;
    --blue: #2f6fd6;
    --white: #ffffff;
    --ink: #0d1f2b;
    --peach: #fde6c0;
    --icon: #1e2a33;
  }
  * { margin: 0; padding: 0; box-sizing: border-box; }
  html, body { width: 847px; height: 1200px; overflow: hidden; background: var(--navy); }
  .flyer { position: relative; width: 847px; height: 1200px; background: var(--navy); color: var(--white); font-family: "Varela Round", sans-serif; }
  .serif { font-family: "Cinzel", serif; }

  .brand { position: absolute; left: 18px; top: 62px; display: flex; align-items: center; gap: 10px; }
  .brand-mark { width: 22px; height: 22px; background: var(--gold); }
  .brand-name { font-family: "Cinzel", serif; font-weight: 700; font-size: 34px; color: var(--gold); letter-spacing: 1px; }

  .headline { position: absolute; left: 18px; top: 180px; width: 360px; font-family: "Cinzel", serif; font-weight: 600; font-size: 31px; line-height: 44px; color: var(--white); }
  .headline .accent { color: var(--blue); }

  .photo { position: absolute; }
  .photo-top { left: 378px; top: 0; width: 469px; height: 313px; background: linear-gradient(135deg, #7b6a58 0%, #c9b39a 45%, #4d5f6e 100%); }
  .photo-bottom { left: 0; top: 903px; width: 423px; height: 297px; background: linear-gradient(120deg, #d8cfc2 0%, #a98a6e 50%, #1f2c44 100%); }

  .section-title { position: absolute; left: 28px; top: 396px; font-family: "Cinzel", serif; font-weight: 600; font-size: 41px; color: var(--gold); letter-spacing: 1px; }

  .card { position: absolute; width: 379px; height: 105px; background: var(--white); color: var(--ink); }
  .card-fha { left: 28px; top: 474px; }
  .card-conv { left: 421px; top: 474px; }
  .card-invest { left: 28px; top: 609px; }
  .card-other { left: 421px; top: 609px; }
  .card-icon { position: absolute; left: 13px; top: 22px; width: 60px; height: 60px; border-radius: 50%; background: var(--peach); }
  .card-icon svg { width: 60px; height: 60px; }
  .card-body { position: absolute; left: 92px; top: 16px; }
  .card-title { font-family: "Cinzel", serif; font-weight: 600; font-size: 18px; letter-spacing: .5px; margin-bottom: 6px; }
  .card-item { font-size: 14px; line-height: 23px; }
  .card-other .card-body { top: 28px; }

  .about { position: absolute; left: 28px; top: 745px; width: 390px; font-size: 14px; line-height: 24.5px; }

  .badge { position: absolute; top: 763px; height: 45px; background: #9aa7b4; }
  .badge-1 { left: 512px; width: 44px; background: #1b3c8f; }
  .badge-2 { left: 583px; width: 54px; background: #d9dde2; border-radius: 4px; }
  .badge-3 { left: 663px; width: 132px; height: 35px; top: 769px; background: #c62d35; }

  .contact { position: absolute; left: 445px; top: 955px; width: 400px; }
  .phone-icon { position: absolute; left: 0; top: 6px; width: 52px; height: 52px; }
  .call-label { position: absolute; left: 64px; top: 5px; font-family: "Cinzel", serif; font-size: 13.5px; white-space: nowrap; }
  .call-number { position: absolute; left: 62px; top: 24px; font-family: "Cinzel", serif; font-size: 38px; white-space: nowrap; }
  .serving { position: absolute; left: 17px; top: 80px; font-family: "Cinzel", serif; font-weight: 600; font-size: 21px; color: var(--gold); white-space: nowrap; }
  .licensed { position: absolute; left: 18px; top: 123px; font-family: "Cinzel", serif; font-weight: 600; font-size: 18px; white-space: nowrap; }
  .nmls { position: absolute; left: 18px; top: 157px; font-family: "Cinzel", serif; font-size: 18px; color: var(--gold); white-space: nowrap; }
  .web { position: absolute; left: 18px; top: 200px; font-family: "Cinzel", serif; font-size: 14px; white-space: nowrap; }
  .web strong { font-size: 18px; font-weight: 400; }
</style>
</head>
<body>
<main class="flyer">
  <div class="brand">
    <span class="brand-mark"></span>
    <span class="brand-name">Harborlane</span>
  </div>

  <h1 class="headline">You open the <span class="accent">Harborlane,</span> we'll carry the load</h1>

  <div class="photo photo-top" role="img" aria-label="Photo of a couple signing mortgage papers with a loan advisor in a bright office"></div>

  <h2 class="section-title">We specialize in...</h2>

  <section class="card card-fha">
    <div class="card-icon">
      <svg viewBox="0 0 60 60" fill="none" stroke="var(--icon)" stroke-width="1.6" stroke-linecap="round">
        <circle cx="38" cy="18" r="7"/><path d="M38 14v8M36 16h3a1.5 1.5 0 0 1 0 3h-2a1.5 1.5 0 0 0 0 3h3"/>
        <path d="M10 42c6-6 12-8 18-6h8a2 2 0 0 1 0 4h-9M36 40l10-6a2 2 0 0 1 2 3l-12 9H14"/>
      </svg>
    </div>
    <div class="card-body">
      <h3 class="card-title">FHA Loans</h3>
      <p class="card-item">* Credit Scores as low as 500</p>
      <p class="card-item">* 203K Renovation Loans</p>
    </div>
  </section>

  <section class="card card-conv">
    <div class="card-icon">
      <svg viewBox="0 0 60 60" fill="none" stroke="var(--icon)" stroke-width="1.6" stroke-linecap="round">
        <path d="M12 22h18l6 4h10M46 18v12M12 22v4"/>
        <circle cx="24" cy="38" r="7"/><path d="M24 34v8"/>
        <path d="M14 32l-2 10 4-3"/>
      </svg>
    </div>
    <div class="card-body">
      <h3 class="card-title">Conventional Loans</h3>
      <p class="card-item">* As little as 1% Down</p>
      <p class="card-item">* Bank Statement for Self-Employed</p>
    </div>
  </section>

  <section class="card card-invest">
    <div class="card-icon">
      <svg viewBox="0 0 60 60" fill="none" stroke="var(--icon)" stroke-width="1.6" stroke-linecap="round">
        <path d="M14 28l16-12 16 12M18 26v18h24V26"/><circle cx="30" cy="27" r="3"/>
        <rect x="34" y="34" width="6" height="10"/>
        <rect x="12" y="34" width="12" height="10" fill="var(--icon)"/>
      </svg>
    </div>
    <div class="card-body">
      <h3 class="card-title">Investor Loans</h3>
      <p class="card-item">* DSCR, &amp; Fix &amp; Flip</p>
      <p class="card-item">* Commercial &amp; New Construction</p>
    </div>
  </section>

  <section class="card card-other">
    <div class="card-icon">
      <svg viewBox="0 0 60 60" fill="none" stroke="var(--icon)" stroke-width="1.6" stroke-linecap="round">
        <rect x="16" y="16" width="28" height="12" rx="2"/><circle cx="30" cy="22" r="4"/>
        <path d="M14 40c5-5 10-6 15-5h7a2 2 0 0 1 0 4h-7M36 38l8-5a2 2 0 0 1 2 3l-10 8H14"/>
      </svg>
    </div>
    <div class="card-body">
      <h3 class="card-title">Other Programs</h3>
      <p class="card-item">* HELOCS &amp; Reverse Mortgages</p>
    </div>
  </section>

  <p class="about">We have served the MD, DC &amp; VA area by providing an array of mortgage loan products tailored to our clients unique needs and desires.</p>

  <span class="badge badge-1"></span>
  <span class="badge badge-2"></span>
  <span class="badge badge-3"></span>

  <div class="photo photo-bottom" role="img" aria-label="Photo of a smiling couple shaking hands with a mortgage advisor in a living room"></div>

  <section class="contact">
    <svg class="phone-icon" viewBox="0 0 52 52" fill="none" stroke="var(--gold)" stroke-width="2.4" stroke-linecap="round" stroke-linejoin="round">
      <path d="M10 6l8 10-4 5c3 7 8 12 15 15l5-4 10 8-5 7C24 46 6 28 4 11z"/>
      <path d="M28 12a12 12 0 0 1 12 12M30 4a20 20 0 0 1 18 18"/>
    </svg>
    <p class="call-label">Call today for a free consultation</p>
    <p class="call-number">(800) 914-6027</p>
    <p class="serving">Serving the DMV since 1997</p>
    <p class="licensed">Licensed Mortgage Company</p>
    <p class="nmls">NMLS #731860</p>
    <p class="web">www.<strong>HARBORLANEHOMELOANS</strong>.com</p>
  </section>
</main>
</body>
</html>
```